Redesign Digital Lending Mobile App - Android/ Flutter

Want to re-theme an existing Digital Lending Mobile app to simplify customer journeys, as well as uplift the UI.

Most users will have small screen phones so the design needs to take that into consideration while also adapting to those with larger devices, like admins with Tablets.

Have already laid out customer journeys on Figma with guidance on how the flow of the app should be. https://www.plankora.example/board/q4ZtRm81KdWe7YhXcvBnaL/LoomKit?frame-id=3-5182&s=Jk2pQwEr7TyUi-9

Video capture of current app: https://vaultbin.example/clip/7Hx3LmQp9RtZw2KcVn4YsBd8EfGj1/play
https://vaultbin.example/clip/4PsWq8ZnTk2LrXy6MbJc3VhGd9FeA/play

The documented views for Web are also here https://docshelf.example/open?ref=3B8F2204AD7C91E5!tk8d1f6a2c4e7b90d3f5a1c8e2b6d4f9a07&cid=3b8f2204ad7c91e5&kind=file%2Cdocx&wdo=2

Target Market(s)

Kenya, Tanzania, Uganda - Africa

Industry/Entity Type

Fintech

Requirements
Must have
• Responsive for diff screens, esp. in context of smaller screen smartphone
Nice to have
• Thematic components to ensure new views can easily be adapted to these themse

```html
<!DOCTYPE html>
<html lang="en">
<head>
<meta charset="utf-8">
<title>LoomKit – Lending App Screens</title>
<link href="https://fonts.googleapis.com/css2?family=Roboto:wght@400;500;700&display=swap" rel="stylesheet">
<style>
  :root{
    --bg:#2f6fc0;
    --brand:#3a7bd0;
    --ink:#1d1d1f;
    --muted:#8a8f98;
    --panel:#eef4fc;
    --card:#f1f6fd;
    --line:#d7dde6;
    --green:#3f9a5f;
    --mint:#c3ecd5;
    --coin:#f5b21f;
    --white:#ffffff;
    --dark:#1f1f1f;
  }
  *{box-sizing:border-box;margin:0;padding:0}
  html,body{width:1200px;height:724px;overflow:hidden}
  body{background:var(--bg);font-family:'Roboto',sans-serif;color:var(--ink);position:relative}
  .screen{position:absolute;top:75px;width:264px;height:571px;background:var(--white);border-radius:22px;overflow:hidden}
  .screen--home{left:103px}
  .screen--summary{left:469px}
  .screen--report{left:836px}
  .abs{position:absolute}
  .top-icon{position:absolute;top:8px;width:16px;height:16px}
  .bell-dot{fill:#e8262b}

  /* brand */
  .brand-name{left:0;width:264px;top:70px;text-align:center;font-size:22px;font-weight:700;color:var(--brand)}

  /* stat chips */
  .stat{position:absolute;width:54px;height:30px;background:var(--card);border-radius:3px;padding:4px 0 0 6px}
  .stat__label{font-size:6px;line-height:8px;display:flex;align-items:center;gap:2px;white-space:nowrap}
  .stat__value{font-size:9px;line-height:11px;font-weight:700;color:var(--brand);margin-top:2px;white-space:nowrap}
  .coin-sm{width:6px;height:6px;border-radius:50%;background:var(--coin);display:inline-block}

  /* filters */
  .filters-title{position:absolute;left:13px;font-size:11px;font-weight:700}
  .dropdown{position:absolute;width:55px;height:23px;border:1px solid var(--line);border-radius:2px;font-size:6px;line-height:8px;text-align:center;padding-top:4px;background:var(--white);white-space:nowrap}
  .dropdown::after{content:"";position:absolute;left:50%;bottom:4px;margin-left:-3px;border-style:solid;border-width:3px 3px 0;border-color:var(--brand) transparent transparent}

  /* home panel */
  .panel{position:absolute;background:var(--panel)}
  .due-row{position:absolute;left:30px;width:206px;height:30px}
  .due-row__coin{position:absolute;left:0;top:0;width:30px;height:30px;border-radius:50%;background:var(--white);border:1px solid #e3e7ee}
  .due-row__coin::after{content:"$";position:absolute;left:7px;top:7px;width:14px;height:14px;border-radius:50%;background:var(--coin);color:var(--white);font-size:9px;font-weight:700;text-align:center;line-height:14px}
  .due-row__label{position:absolute;left:38px;top:1px;font-size:7.5px;line-height:9px;font-weight:500}
  .due-row__amount{position:absolute;right:0;top:1px;font-size:7.5px;line-height:9px;font-weight:500}
  .due-row__track{position:absolute;left:38px;right:0;top:13px;height:3px;background:var(--white);border-radius:2px}
  .due-row__fill{position:absolute;left:0;top:0;width:81px;height:3px;background:var(--green);border-radius:2px}
  .due-row__knob{position:absolute;left:78px;top:-2px;width:7px;height:7px;border-radius:50%;background:var(--brand);border:1px solid var(--white)}
  .growth-art{position:absolute;left:30px;top:387px;width:204px;height:97px;background:linear-gradient(135deg,#ffffff 0%,#e8f1fb 55%,#9cc8ee 100%)}

  .btn-next{position:absolute;left:107px;top:494px;width:56px;height:16px;border-radius:8px;background:var(--green);color:var(--white);font-size:7.5px;font-weight:700;display:flex;align-items:center;justify-content:center;gap:5px}

  /* nav */
  .nav{position:absolute;left:0;bottom:0;width:264px;height:50px;background:var(--brand)}
  .nav svg{position:absolute;top:11px;width:18px;height:18px}
  .nav__bar{position:absolute;left:90px;bottom:10px;width:84px;height:2px;background:var(--white);border-radius:1px}

  /* summary */
  .screen-title{position:absolute;left:0;width:264px;text-align:center;font-size:17px;font-weight:700;color:var(--brand)}
  .detail-row{position:absolute;left:30px;width:206px;height:28px}
  .detail-row__label{position:absolute;left:0;width:145px;height:28px;background:var(--white);font-size:7px;line-height:28px;padding-left:10px}
  .detail-row__value{position:absolute;left:151px;width:55px;height:28px;background:var(--mint);font-size:7px;line-height:28px;text-align:center;white-space:nowrap}

  /* report */
  .total-label{position:absolute;left:0;width:264px;top:81px;text-align:center;font-size:13px}
  .total-value{position:absolute;left:0;width:264px;top:98px;text-align:center;font-size:17px;font-weight:700;color:var(--green)}
  .pill{position:absolute;top:202px;width:56px;height:16px;border-radius:8px;color:var(--white);font-size:7px;font-weight:700;text-align:center;line-height:16px}
  .pill--profit{left:70px;background:var(--green)}
  .pill--loss{left:134px;background:var(--dark)}
  .chart-card{position:absolute;left:33px;top:228px;width:198px;height:154px;background:var(--white);border-radius:3px}
  .chart-art{position:absolute;left:45px;top:258px;width:174px;height:118px;background:linear-gradient(90deg,#d9ecf9 0%,#f3e7c9 50%,#e6ddf0 100%);border-radius:2px}
  .period{position:absolute;top:242px;font-size:6px;line-height:8px;color:var(--muted);transform:translateX(-50%)}
  .period--active{border:1px solid #f0a060;border-radius:3px;padding:1px 4px;top:240px}
  .week{position:absolute;top:387px;font-size:6px;line-height:8px;color:var(--muted);transform:translateX(-50%)}
</style>
</head>
<body>

<section class="screen screen--home">
  <svg class="top-icon" style="left:208px" viewBox="0 0 16 16" fill="none" stroke="#222" stroke-width="1.2"><circle cx="8" cy="5.5" r="3"/><path d="M2.5 15c0-3.5 2.5-5.5 5.5-5.5s5.5 2 5.5 5.5"/></svg>
  <svg class="top-icon" style="left:236px" viewBox="0 0 16 16" fill="none" stroke="#222" stroke-width="1.2"><path d="M4 11V7a4 4 0 0 1 8 0v4l1.5 1.5h-11z"/><path d="M6.5 14h3"/><circle class="bell-dot" cx="12.5" cy="3.5" r="2.5" stroke="none"/></svg>

  <div class="abs brand-name">LoomKit</div>

  <div class="stat" style="left:13px;top:118px"><div class="stat__label"><span class="coin-sm"></span>Disbursed</div><div class="stat__value">$ 30,000</div></div>
  <div class="stat" style="left:73px;top:118px"><div class="stat__label"><span class="coin-sm"></span>Collected</div><div class="stat__value">$ 20,000</div></div>
  <div class="stat" style="left:133px;top:118px"><div class="stat__label"><span class="coin-sm"></span>Active Client</div><div class="stat__value">50 clients</div></div>
  <div class="stat" style="left:193px;top:118px"><div class="stat__label"><span class="coin-sm"></span>New Client</div><div class="stat__value">30 clients</div></div>

  <div class="filters-title" style="top:161px">Filters :</div>
  <div class="dropdown" style="left:13px;top:183px">Loan Officer</div>
  <div class="dropdown" style="left:73px;top:183px">Branch</div>
  <div class="dropdown" style="left:133px;top:183px">Fund</div>
  <div class="dropdown" style="left:193px;top:183px">Product</div>

  <div class="panel" style="left:13px;top:212px;width:235px;height:309px"></div>

  <div class="due-row" style="top:227px"><div class="due-row__coin"></div><div class="due-row__label">Near due</div><div class="due-row__amount">$ 25,000</div><div class="due-row__track"><div class="due-row__fill"></div><div class="due-row__knob"></div></div></div>
  <div class="due-row" style="top:267px"><div class="due-row__coin"></div><div class="due-row__label">Due</div><div class="due-row__amount">$ 34,000</div><div class="due-row__track"><div class="due-row__fill"></div><div class="due-row__knob"></div></div></div>
  <div class="due-row" style="top:307px"><div class="due-row__coin"></div><div class="due-row__label">Pending Depursement</div><div class="due-row__amount">$ 30,000</div><div class="due-row__track"><div class="due-row__fill"></div><div class="due-row__knob"></div></div></div>
  <div class="due-row" style="top:347px"><div class="due-row__coin"></div><div class="due-row__label">Active Loan</div><div class="due-row__amount">$ 20,000</div><div class="due-row__track"><div class="due-row__fill"></div><div class="due-row__knob"></div></div></div>

  <div class="growth-art" role="img" aria-label="Illustration of a rising growth arrow over a line graph"></div>

  <div class="btn-next">Next <svg width="10" height="8" viewBox="0 0 10 8" fill="none" stroke="#fff" stroke-width="1.2"><path d="M0 4h9M6 1l3 3-3 3"/></svg></div>

  <nav class="nav">
    <svg style="left:29px" viewBox="0 0 18 18" fill="none" stroke="#fff" stroke-width="1.2"><path d="M3 8l6-5 6 5v8H3z"/><path d="M7 13h4"/></svg>
    <svg style="left:76px" viewBox="0 0 18 18" fill="none" stroke="#fff" stroke-width="1.2"><circle cx="11" cy="6" r="4.5"/><path d="M9 8l4-4"/><path d="M1 13l4-2h4l2 1h4l-5 4H4"/></svg>
    <svg style="left:123px" viewBox="0 0 18 18" fill="none" stroke="#fff" stroke-width="1.2"><path d="M9 3H3v12h12V9"/><path d="M8 10l7-7 1 1-7 7H8z"/></svg>
    <svg style="left:170px" viewBox="0 0 18 18" fill="none" stroke="#fff" stroke-width="1.2"><path d="M4 2h7l3 3v11H4z"/><path d="M7 8h5M7 11h5M7 14h3"/></svg>
    <svg style="left:216px" viewBox="0 0 18 18" fill="none" stroke="#fff" stroke-width="1.2"><circle cx="9" cy="9" r="2.5"/><path d="M9 1.5l1.5 2 2.5-.5.5 2.5 2 1.5-1 2.3 1 2.2-2 1.5-.5 2.5-2.5-.5L9 16.5l-1.5-2-2.5.5-.5-2.5-2-1.5 1-2.2-1-2.3 2-1.5.5-2.5 2.5.5z"/></svg>
    <div class="nav__bar"></div>
  </nav>
</section>

<section class="screen screen--summary">
  <svg class="top-icon" style="left:16px" viewBox="0 0 16 16" fill="none" stroke="#222" stroke-width="1.3"><circle cx="6.5" cy="6.5" r="4.5"/><path d="M10 10l4 4"/></svg>
  <svg class="top-icon" style="left:208px" viewBox="0 0 16 16" fill="none" stroke="#222" stroke-width="1.2"><circle cx="8" cy="5.5" r="3"/><path d="M2.5 15c0-3.5 2.5-5.5 5.5-5.5s5.5 2 5.5 5.5"/></svg>
  <svg class="top-icon" style="left:236px" viewBox="0 0 16 16" fill="none" stroke="#222" stroke-width="1.2"><path d="M4 11V7a4 4 0 0 1 8 0v4l1.5 1.5h-11z"/><path d="M6.5 14h3"/><circle class="bell-dot" cx="12.5" cy="3.5" r="2.5" stroke="none"/></svg>

  <h1 class="screen-title" style="top:34px">Loan Summary</h1>

  <div class="filters-title" style="top:84px">Filters :</div>
  <div class="dropdown" style="left:13px;top:105px">Loan Officer</div>
  <div class="dropdown" style="left:73px;top:105px">Branch</div>
  <div class="dropdown" style="left:133px;top:105px">Fund</div>
  <div class="dropdown" style="left:193px;top:105px">Product</div>

  <div class="panel" style="left:15px;top:143px;width:234px;height:331px"></div>

  <div class="detail-row" style="top:159px"><div class="detail-row__label">Loan reference no</div><div class="detail-row__value">3213</div></div>
  <div class="detail-row" style="top:193px"><div class="detail-row__label">Loan Status</div><div class="detail-row__value">Active</div></div>
  <div class="detail-row" style="top:227px"><div class="detail-row__label">Date disbursed</div><div class="detail-row__value">July 13, 2024</div></div>
  <div class="detail-row" style="top:261px"><div class="detail-row__label">Date approved</div><div class="detail-row__value">July 20,2024</div></div>
  <div class="detail-row" style="top:295px"><div class="detail-row__label">Last repayment date</div><div class="detail-row__value">July 27,2024</div></div>
  <div class="detail-row" style="top:329px"><div class="detail-row__label">Last repayment date</div><div class="detail-row__value">July 27,2024</div></div>
  <div class="detail-row" style="top:363px"><div class="detail-row__label">Amount disbursed</div><div class="detail-row__value">30,000</div></div>
  <div class="detail-row" style="top:397px"><div class="detail-row__label">Amount Outstanding</div><div class="detail-row__value">30,000</div></div>
  <div class="detail-row" style="top:431px"><div class="detail-row__label">Over due days</div><div class="detail-row__value">30</div></div>

  <div class="btn-next">Next <svg width="10" height="8" viewBox="0 0 10 8" fill="none" stroke="#fff" stroke-width="1.2"><path d="M0 4h9M6 1l3 3-3 3"/></svg></div>

  <nav class="nav">
    <svg style="left:29px" viewBox="0 0 18 18" fill="none" stroke="#fff" stroke-width="1.2"><path d="M3 8l6-5 6 5v8H3z"/><path d="M7 13h4"/></svg>
    <svg style="left:76px" viewBox="0 0 18 18" fill="none" stroke="#fff" stroke-width="1.2"><circle cx="11" cy="6" r="4.5"/><path d="M9 8l4-4"/><path d="M1 13l4-2h4l2 1h4l-5 4H4"/></svg>
    <svg style="left:123px" viewBox="0 0 18 18" fill="none" stroke="#fff" stroke-width="1.2"><path d="M9 3H3v12h12V9"/><path d="M8 10l7-7 1 1-7 7H8z"/></svg>
    <svg style="left:170px" viewBox="0 0 18 18" fill="none" stroke="#fff" stroke-width="1.2"><path d="M4 2h7l3 3v11H4z"/><path d="M7 8h5M7 11h5M7 14h3"/></svg>
    <svg style="left:216px" viewBox="0 0 18 18" fill="none" stroke="#fff" stroke-width="1.2"><circle cx="9" cy="9" r="2.5"/><path d="M9 1.5l1.5 2 2.5-.5.5 2.5 2 1.5-1 2.3 1 2.2-2 1.5-.5 2.5-2.5-.5L9 16.5l-1.5-2-2.5.5-.5-2.5-2-1.5 1-2.2-1-2.3 2-1.5.5-2.5 2.5.5z"/></svg>
    <div class="nav__bar"></div>
  </nav>
</section>

<section class="screen screen--report">
  <svg class="top-icon" style="left:208px" viewBox="0 0 16 16" fill="none" stroke="#222" stroke-width="1.2"><circle cx="8" cy="5.5" r="3"/><path d="M2.5 15c0-3.5 2.5-5.5 5.5-5.5s5.5 2 5.5 5.5"/></svg>
  <svg class="top-icon" style="left:236px" viewBox="0 0 16 16" fill="none" stroke="#222" stroke-width="1.2"><path d="M4 11V7a4 4 0 0 1 8 0v4l1.5 1.5h-11z"/><path d="M6.5 14h3"/><circle class="bell-dot" cx="12.5" cy="3.5" r="2.5" stroke="none"/></svg>

  <h1 class="screen-title" style="top:49px">Report</h1>
  <div class="total-label">Total Loan</div>
  <div class="total-value">$ 35,000,000</div>

  <div class="filters-title" style="top:126px">Filters :</div>
  <div class="dropdown" style="left:13px;top:147px">Loan Officer</div>
  <div class="dropdown" style="left:73px;top:147px">Branch</div>
  <div class="dropdown" style="left:133px;top:147px">Fund</div>
  <div class="dropdown" style="left:193px;top:147px">Product</div>

  <div class="panel" style="left:14px;top:185px;width:235px;height:218px"></div>
  <div class="pill pill--profit">Profit</div>
  <div class="pill pill--loss">Loss</div>

  <div class="chart-card"></div>
  <span class="period" style="left:58px">DAY</span>
  <span class="period" style="left:107px">WEEK</span>
  <span class="period period--active" style="left:155px">MONTH</span>
  <span class="period" style="left:204px">YEAR</span>

  <div class="chart-art" role="img" aria-label="Illustrated weekly profit chart with coloured columns"></div>

  <span class="week" style="left:57px">WEEK 1</span>
  <span class="week" style="left:106px">WEEK 2</span>
  <span class="week" style="left:156px">WEEK 3</span>
  <span class="week" style="left:205px">WEEK 4</span>

  <div class="stat" style="left:13px;top:425px"><div class="stat__label"><span class="coin-sm"></span>Revenue</div><div class="stat__value">$ 300</div></div>
  <div class="stat" style="left:73px;top:425px"><div class="stat__label"><span class="coin-sm"></span>Expenses</div><div class="stat__value">$ 350</div></div>
  <div class="stat" style="left:133px;top:425px"><div class="stat__label"><span class="coin-sm"></span>Tax</div><div class="stat__value">$ 200</div></div>
  <div class="stat" style="left:193px;top:425px"><div class="stat__label"><span class="coin-sm"></span>Salaries</div><div class="stat__value">3500</div></div>

  <nav class="nav">
    <svg style="left:29px" viewBox="0 0 18 18" fill="none" stroke="#fff" stroke-width="1.2"><path d="M3 8l6-5 6 5v8H3z"/><path d="M7 13h4"/></svg>
    <svg style="left:76px" viewBox="0 0 18 18" fill="none" stroke="#fff" stroke-width="1.2"><circle cx="11" cy="6" r="4.5"/><path d="M9 8l4-4"/><path d="M1 13l4-2h4l2 1h4l-5 4H4"/></svg>
    <svg style="left:123px" viewBox="0 0 18 18" fill="none" stroke="#fff" stroke-width="1.2"><path d="M9 3H3v12h12V9"/><path d="M8 10l7-7 1 1-7 7H8z"/></svg>
    <svg style="left:170px" viewBox="0 0 18 18" fill="none" stroke="#fff" stroke-width="1.2"><path d="M4 2h7l3 3v11H4z"/><path d="M7 8h5M7 11h5M7 14h3"/></svg>
    <svg style="left:216px" viewBox="0 0 18 18" fill="none" stroke="#fff" stroke-width="1.2"><circle cx="9" cy="9" r="2.5"/><path d="M9 1.5l1.5 2 2.5-.5.5 2.5 2 1.5-1 2.3 1 2.2-2 1.5-.5 2.5-2.5-.5L9 16.5l-1.5-2-2.5.5-.5-2.5-2-1.5 1-2.2-1-2.3 2-1.5.5-2.5 2.5.5z"/></svg>
    <div class="nav__bar"></div>
  </nav>
</section>

</body>
</html>
```